Compnay PowerPoint Tempalte Design

I am needing a good base design and slide designs for interior and exterior company presentations. The template will need to be on the company brand with proper coloring and fonts. Able to be creative with layout options with a good example attached.
website for reference: www.crewvlt.com/

Target Market(s)

Professionals

Font styles to use
Other font styles liked:
• Helvetica

Requirements
Must have
• On Brand Colors, Clean, simple design

```html
<!DOCTYPE html>
<html lang="en">
<head>
<meta charset="utf-8">
<title>VLT Presentation Template</title>
<link href="https://fonts.googleapis.com/css2?family=Arimo:wght@400;700&display=swap" rel="stylesheet">
<style>
:root{
  --board:#7b7b7b;
  --teal:#2f8a78;
  --forest:#1d4a40;
  --blue:#11668f;
  --ink:#1c1c1c;
  --body:#3a3a3a;
  --white:#ffffff;
  --paper:#f3f3f3;
}
*{margin:0;padding:0;box-sizing:border-box}
html,body{width:1200px;height:1091px;overflow:hidden;background:var(--board);font-family:'Arimo',Helvetica,Arial,sans-serif}
.board{position:relative;width:1200px;height:1091px;overflow:hidden}
.board-accent{position:absolute;inset:0}
.slide{position:absolute;width:511px;height:287px;overflow:hidden;background:var(--white);box-shadow:0 6px 18px rgba(0,0,0,.35)}
.slide svg.shapes{position:absolute;inset:0}
.photo{position:absolute}
.wordmark{position:absolute;font-weight:700;letter-spacing:.5px;line-height:1}
.wordmark-dark{color:var(--ink)}
.wordmark-light{color:var(--white)}

/* cover */
.s-cover{left:74px;top:78px}
.s-cover .photo{left:18px;top:51px;width:475px;height:223px;background:linear-gradient(100deg,#6d7a84 0%,#3b4f63 35%,#2a3a48 60%,#4d6c82 100%)}
.s-cover .wordmark{left:25px;top:54px;font-size:22px}
.cover-title{position:absolute;left:200px;top:172px;width:160px;text-align:center;color:var(--white)}
.cover-title h1{font-size:31px;font-weight:700}
.cover-title p{font-size:6.3px;line-height:10.3px;margin-top:6px}

/* values */
.s-values{left:615px;top:78px;background:none}
.s-values .photo{inset:0;background:linear-gradient(120deg,#1f6b72 0%,#175f6a 45%,#2b7d86 75%,#1c6670 100%)}
.values-text{position:absolute;left:35px;top:98px;color:var(--white);width:230px}
.values-text h2{font-size:30px;font-weight:700;line-height:36px;letter-spacing:.3px}
.values-text p{font-size:8.8px;line-height:15.8px;margin-top:19px}
.s-values .wordmark{right:24px;bottom:14px;font-size:12px}

/* services */
.s-services{left:74px;top:402px;background:linear-gradient(135deg,var(--white) 0%,var(--paper) 60%,#ebebeb 100%)}
.slide-heading{position:absolute;color:var(--teal);font-weight:700;font-size:31px;letter-spacing:.2px}
.s-services .slide-heading{left:24px;top:20px}
.s-services .wordmark{right:31px;top:44px;font-size:11px}
.service-label{position:absolute;top:222px;width:120px;margin-left:-60px;text-align:center;color:var(--white);font-weight:700;font-size:10.5px}

/* testimonials */
.s-testimonials{left:615px;top:402px}
.s-testimonials .slide-heading{left:33px;top:22px}
.s-testimonials .wordmark{right:33px;top:46px;font-size:11px}
.avatar{position:absolute;left:233px;top:91px;width:43px;height:43px;border-radius:50%;background:radial-gradient(circle at 50% 40%,#8a6a58,#2a2a2a 70%)}
.quote-mark{position:absolute;left:272px;top:82px;color:var(--blue);font-size:58px;font-weight:700;line-height:1}
.quote{position:absolute;left:80px;top:139px;width:350px;text-align:center;font-size:8.8px;line-height:18px;color:var(--body)}
.quote-author{position:absolute;left:0;width:511px;top:244px;text-align:center;font-size:11px;font-weight:700;color:var(--ink)}

/* about */
.s-about{left:74px;top:726px}
.s-about .slide-heading{left:250px;top:30px;font-size:30px}
.about-text{position:absolute;left:250px;top:80px;width:258px;font-size:8.9px;line-height:17.85px;color:var(--body)}
.s-about .wordmark{right:21px;bottom:14px;font-size:11px}

/* closing */
.s-thanks{left:615px;top:726px}
.s-thanks .photo{inset:0;background:linear-gradient(100deg,#e9e2b8 0%,#d9e0d3 35%,#e8e6cf 60%,#cfd6d6 100%)}
.s-thanks .wordmark{left:8px;top:44px;font-size:20px}
.thanks-band{position:absolute;left:65px;top:212px;width:380px;height:75px;background:var(--blue);color:var(--white);font-size:57px;text-align:center;line-height:75px;letter-spacing:1px}
</style>
</head>
<body>
<main class="board">
  <svg class="board-accent" width="1200" height="1091" viewBox="0 0 1200 1091" aria-hidden="true">
    <polygon points="0,0 283,0 0,212" fill="var(--blue)"/>
    <polygon points="1200,702 911,1091 1200,1091" fill="var(--teal)"/>
  </svg>

  <section class="slide s-cover">
    <div class="photo" role="img" aria-label="Group photo of five smiling team members standing together"></div>
    <svg class="shapes" width="511" height="287" viewBox="0 0 511 287" aria-hidden="true">
      <polygon points="330,0 150,287 511,287" fill="var(--teal)" opacity=".72"/>
      <polygon points="420,230 352,287 511,287 511,205" fill="var(--blue)"/>
    </svg>
    <div class="wordmark wordmark-dark">VLT</div>
    <div class="cover-title">
      <h1>VLT</h1>
      <p>Where we maintain a passion for excellence, striving to be better each and every day, so that our guests leave happy and our team members feel fulfilled.</p>
    </div>
  </section>

  <section class="slide s-values">
    <div class="photo" role="img" aria-label="Silhouettes of business people in a glass office, tinted teal"></div>
    <div class="values-text">
      <h2>OUR CORE<br>VALUES</h2>
      <p>Our culture is founded on four core values and the entrepreneurial spirit of ownership that comes from a foundation of passion for our people, commitment to our business, transparency, and continued progress.</p>
    </div>
    <div class="wordmark wordmark-light">VLT</div>
  </section>

  <section class="slide s-services">
    <h2 class="slide-heading">WHAT WE DO</h2>
    <div class="wordmark wordmark-dark">VLT</div>
    <svg class="shapes" width="511" height="287" viewBox="0 0 511 287">
      <defs>
        <linearGradient id="kitchen" x1="0" y1="0" x2="0" y2="1"><stop offset="0" stop-color="#d9d4cc"/><stop offset=".6" stop-color="#b07a4a"/><stop offset="1" stop-color="#5a5a5a"/></linearGradient>
        <linearGradient id="keys" x1="0" y1="0" x2="1" y2="1"><stop offset="0" stop-color="#e6e1da"/><stop offset=".5" stop-color="#c79a7e"/><stop offset="1" stop-color="#8a6a52"/></linearGradient>
        <linearGradient id="signing" x1="0" y1="0" x2="1" y2="1"><stop offset="0" stop-color="#d8c8b4"/><stop offset=".5" stop-color="#eef0f2"/><stop offset="1" stop-color="#c49a88"/></linearGradient>
      </defs>
      <polygon points="111,82 205,176 111,270 17,176" fill="var(--teal)"/>
      <polygon points="111,82 178,149 111,216 44,149" fill="url(#kitchen)" role="img" aria-label="Restaurant kitchen counter with shelves"/>
      <polygon points="255,82 349,176 255,270 161,176" fill="var(--forest)"/>
      <polygon points="255,82 322,149 255,216 188,149" fill="url(#keys)" role="img" aria-label="Hand holding house keys"/>
      <polygon points="399,82 493,176 399,270 305,176" fill="var(--blue)"/>
      <polygon points="399,82 466,149 399,216 332,149" fill="url(#signing)" role="img" aria-label="Hands signing a document"/>
    </svg>
    <div class="service-label" style="left:111px">Restaurants</div>
    <div class="service-label" style="left:255px">Real Estate</div>
    <div class="service-label" style="left:399px">Development</div>
  </section>

  <section class="slide s-testimonials">
    <svg class="shapes" width="511" height="287" viewBox="0 0 511 287" aria-hidden="true">
      <polygon points="0,210 0,287 12,287" fill="var(--forest)"/>
      <polygon points="50,193 8,220 0,287 105,287" fill="var(--blue)"/>
      <polygon points="471,135 511,195 511,287 440,287" fill="var(--teal)"/>
      <polygon points="420,215 378,287 511,287 511,270" fill="var(--blue)"/>
      <polygon points="462,236 511,267 511,287 440,287" fill="var(--forest)"/>
    </svg>
    <h2 class="slide-heading">TESTIMONIALS</h2>
    <div class="wordmark wordmark-dark">VLT</div>
    <div class="avatar" role="img" aria-label="Portrait of the client giving the testimonial"></div>
    <div class="quote-mark">&ldquo;</div>
    <p class="quote">Sed ut perspiciatis unde omnis iste natus error sit voluptatem accusantium doloremque laudantium, totam rem aperiam, eaque ipsa quae ab illo inventore veritatis et quasi architecto beatae vitae dicta sunt explicabo. Nemo enim ipsam voluptatem quia voluptas sit aspernatur aut odit aut fugit, sed quia consequuntur magni dolores eos qui ratione voluptatem sequi nesciunt.</p>
    <p class="quote-author">- Northline Media</p>
  </section>

  <section class="slide s-about">
    <svg class="shapes" width="511" height="287" viewBox="0 0 511 287">
      <defs>
        <linearGradient id="cafe" x1="0" y1="0" x2="1" y2="1"><stop offset="0" stop-color="#3b7d6d"/><stop offset=".5" stop-color="#1f4c42"/><stop offset="1" stop-color="#2d6f60"/></linearGradient>
      </defs>
      <polygon points="110,0 125,173 196,131 285,287 0,287 0,124" fill="url(#cafe)" role="img" aria-label="Friends sharing coffee at a cafe, tinted green"/>
      <polygon points="0,205 0,287 135,287 95,250" fill="var(--forest)" opacity=".9"/>
      <polygon points="215,185 285,287 135,287" fill="var(--blue)"/>
    </svg>
    <h2 class="slide-heading">About</h2>
    <p class="about-text">VLT is dedicated to cultivating a positive culture of leadership for its team members' professional and personal development, and this person-focused mentality transfers throughout the company from partners to our teams to guests. We strive to ensure each team member feels valued in all aspects of their role, reinforcing the importance of fostering a self-sustaining culture of success where everyone makes a team effort to communicate and overcome adversity.</p>
    <div class="wordmark wordmark-dark">VLT</div>
  </section>

  <section class="slide s-thanks">
    <div class="photo" role="img" aria-label="Four smiling business professionals standing in a bright office"></div>
    <div class="wordmark wordmark-dark">VLT</div>
    <div class="thanks-band">THANK YOU</div>
  </section>
</main>
</body>
</html>
```